Small Business Consulting Firm Needs Letterhead

We need a letterhead for our company "Brightpath Plus". Our company does outbound calling and mailing to business owner's companies who have taken high interest loans. These loans tend to put these businesses in a big financial bind short term, and we help them find better financial options. We would like the design to match our colors of our logo. Headers and footers would look nice, but we are open. We would want it to include our address, website, phone, and email info. Our address - 2000 E. Lamar Blvd. Suite 600Website - www.safeguardtoday.comEmail - info@safeguardtoday.comPhone - 855-726-1938
Industry/Entity Type
Financial Planning
Look and feel
Each slider illustrates characteristics of the customer's brand and the style your logo design should communicate.

```html
<!DOCTYPE html>
<html lang="en">
<head>
<meta charset="utf-8">
<title>Brightpath Plus Letterhead</title>
<link rel="stylesheet" href="https://fonts.googleapis.com/css2?family=Lato:wght@400;700&family=Allura&display=swap">
<style>
  :root {
    --brand-green: #7aba43;
    --brand-blue: #0d7fc4;
    --ink: #1f1f1f;
    --ink-soft: #3c3c3c;
    --paper: #ffffff;
    --backdrop: #e4e4e4;
  }
  * { box-sizing: border-box; margin: 0; padding: 0; }
  html, body {
    width: 1200px; height: 1200px; overflow: hidden;
    background: var(--backdrop);
    font-family: "Lato", Arial, sans-serif;
    color: var(--ink);
  }
  .letterhead {
    position: absolute; left: 160px; top: 31px;
    width: 880px; height: 1138px;
    background: var(--paper);
    overflow: hidden;
  }
  .header-band {
    position: absolute; left: 0; top: 0; width: 880px; height: 44px;
    background: var(--brand-green);
  }
  .header-rule {
    position: absolute; left: 0; top: 52px; width: 880px; height: 10px;
    background: var(--brand-blue);
  }
  .brand {
    position: absolute; left: 46px; top: 144px;
    display: flex; align-items: center; gap: 10px;
  }
  .brand-mark { width: 16px; height: 16px; background: var(--brand-blue); }
  .brand-name {
    font-size: 17px; font-weight: 400; letter-spacing: 1.6px;
    text-transform: uppercase; color: var(--ink-soft);
  }
  .letter-date {
    position: absolute; right: 50px; top: 246px;
    font-size: 10.5px;
  }
  .letter-date strong { font-weight: 700; }
  .letter-body {
    position: absolute; left: 48px; top: 309px; width: 784px;
  }
  .salutation {
    color: var(--brand-blue); font-weight: 700; font-size: 12.5px;
    margin-bottom: 24px;
  }
  .letter-body p.copy {
    font-size: 10.2px; line-height: 16.7px; text-align: justify;
    margin-bottom: 15px; hyphens: auto;
  }
  .closing {
    position: absolute; left: 48px; top: 770px;
    font-size: 11.5px; font-weight: 700;
  }
  .signature {
    position: absolute; left: 44px; top: 786px;
    font-family: "Allura", cursive; font-size: 56px; color: var(--ink);
  }
  .contact-line {
    position: absolute; left: 48px; top: 1063px;
    display: flex; gap: 22px; font-size: 10px; color: var(--ink-soft);
  }
  .contact-item { display: flex; align-items: center; gap: 7px; }
  .contact-item svg { width: 10px; height: 10px; fill: var(--brand-blue); }
  .footer-rule {
    position: absolute; left: 0; bottom: 44px; width: 880px; height: 5px;
    background: var(--brand-green);
  }
  .footer-band {
    position: absolute; left: 0; bottom: 0; width: 880px; height: 38px;
    background: var(--brand-blue);
    display: flex; align-items: center; justify-content: flex-end;
    padding-right: 48px;
  }
  .footer-address {
    display: flex; align-items: center; gap: 9px;
    color: #fff; font-size: 13px; letter-spacing: 0.8px;
  }
  .footer-address svg { width: 11px; height: 15px; fill: #fff; }
</style>
</head>
<body>
<main class="letterhead">
  <div class="header-band" aria-hidden="true"></div>
  <div class="header-rule" aria-hidden="true"></div>

  <div class="brand">
    <span class="brand-mark"></span>
    <span class="brand-name">Brightpath Plus</span>
  </div>

  <div class="letter-date"><strong>Date:</strong> 24, August, 2019</div>

  <section class="letter-body">
    <p class="salutation">Dear Alan Pierce,</p>
    <p class="copy">Lorem ipsum dolor sit amet, consectetur adipiscing elit. Curabitur a arcu sagittis, convallis dolor a, gravida lectus. Duis efficitur ipsum ut aliquet scelerisque. Suspendisse eu fermentum metus. Suspendisse ac hendrerit elit. Sed gravida augue tellus, vitae facilisis sapien sodales ac. Curabitur a justo vel lectus tincidunt lobortis eu in lorem. Cras facilisis massa et malesuada sagittis. Aliquam vel nulla aliquet, sollicitudin lorem eget, cursus ligula. Donec a diam facilisis, consectetur ipsum in, posuere tellus. Donec non eros semper, rhoncus dolor ac, auctor elit. In euismod ultrices nisi, vitae volutpat lectus gravida quis. Aliquam accumsan ipsum a nisl volutpat blandit. Praesent venenatis risus a molestie placerat. Ut sagittis mauris non tincidunt fringilla. Sed consectetur diam nec enim gravida, vel gravida mauris aliquam.</p>
    <p class="copy">Pellentesque sit amet nisi viverra, mollis ex at, convallis lacus. Curabitur aliquet vitae arcu vel convallis. Aenean et dictum libero. Mauris tellus nibh, venenatis ac felis sed, vehicula efficitur lectus. Curabitur et ipsum turpis. Ut laoreet maximus viverra. Nunc accumsan velit sit amet lacinia hendrerit. Quisque facilisis nisi at fringilla pretium. Aliquam justo nulla, aliquam et risus at, porttitor pulvinar est. Nam volutpat rutrum venenatis. Praesent tempus nibh risus.</p>
    <p class="copy">Aliquam posuere massa a magna rutrum, id cursus eros viverra. Proin dignissim nunc in mauris tempus, in consequat lacus ultrices. Morbi bibendum non leo sed faucibus. Aliquam pharetra elit in maximus consectetur. In cursus tristique ornare. Nam facilisis sapien in ante tempor consectetur vitae at augue. Proin posuere in massa vitae finibus. Nullam sit amet posuere urna, quis fermentum mi. Pellentesque vel quam in enim tempor venenatis ac ac ligula. Praesent imperdiet euismod elit non ultrices. Pellentesque sed orci et sapien tempus laoreet. Vestibulum felis enim, vestibulum sit amet enim eget, sagittis consectetur neque.</p>
    <p class="copy">Curabitur quam leo, pharetra nec porttitor quis, blandit at orci. Nunc a augue cursus, mollis felis quis, fringilla neque. Proin non augue id lectus tempor lacinia et efficitur elit. Ut scelerisque nibh interdum, hendrerit erat at, pellentesque diam. Sed et venenatis elit, quis mattis metus. Donec rhoncus non ante id commodo. Maecenas commodo non ex sit amet fermentum. Maecenas volutpat, neque at bibendum ullamcorper, odio diam convallis urna, nec pharetra neque justo sit amet orci. Proin et tellus tellus. Praesent ultricies dolor lacinia venenatis dapibus. Proin pharetra bibendum nisl, at congue nibh tincidunt efficitur. Sed egestas eget tellus iaculis mollis.</p>
    <p class="copy">Cras tincidunt ornare lectus, eget sodales ex varius ac. Nunc luctus sollicitudin nisi. Quisque quis dictum ex. Quisque iaculis, tortor porta sagittis blandit, erat leo dapibus nisi, varius gravida mi libero vel lacus. Proin a viverra diam, eu ultrices leo. Curabitur vel ipsum a erat sodales placerat. Etiam eu consectetur augue.</p>
  </section>

  <p class="closing">Sincerely Your,</p>
  <p class="signature">Signature</p>

  <div class="contact-line">
    <span class="contact-item">
      <svg viewBox="0 0 10 10" aria-hidden="true"><path d="M1 3 Q1 1 3 1 L7 1 Q9 1 9 3 L8 4 L6.5 3.3 L6.5 2.5 L3.5 2.5 L3.5 3.3 L2 4 Z M2.5 5 L7.5 5 L8.5 9 L1.5 9 Z"/></svg>
      855-726-1938
    </span>
    <span class="contact-item">
      <svg viewBox="0 0 10 10" aria-hidden="true"><path d="M0.5 2 L9.5 2 L5 5.5 Z M0.5 3 L5 6.5 L9.5 3 L9.5 8.5 L0.5 8.5 Z"/></svg>
      info@brightpathplus.com
    </span>
    <span class="contact-item">
      <svg viewBox="0 0 10 10" aria-hidden="true"><path d="M5 0.5 A4.5 4.5 0 1 0 5 9.5 A4.5 4.5 0 1 0 5 0.5 Z M5 1.6 Q6.6 3 6.7 4.5 L3.3 4.5 Q3.4 3 5 1.6 Z M3.3 5.5 L6.7 5.5 Q6.6 7 5 8.4 Q3.4 7 3.3 5.5 Z M1.6 4.5 Q1.9 2.6 3.6 1.8 Q2.5 3 2.3 4.5 Z M1.6 5.5 L2.3 5.5 Q2.5 7 3.6 8.2 Q1.9 7.4 1.6 5.5 Z M8.4 4.5 L7.7 4.5 Q7.5 3 6.4 1.8 Q8.1 2.6 8.4 4.5 Z M8.4 5.5 Q8.1 7.4 6.4 8.2 Q7.5 7 7.7 5.5 Z"/></svg>
      www.brightpathplus.com
    </span>
  </div>

  <div class="footer-rule" aria-hidden="true"></div>
  <footer class="footer-band">
    <div class="footer-address">
      <svg viewBox="0 0 11 15" aria-hidden="true"><path d="M5.5 0 A5.5 5.5 0 0 1 11 5.5 C11 9 5.5 15 5.5 15 C5.5 15 0 9 0 5.5 A5.5 5.5 0 0 1 5.5 0 Z M5.5 3.3 A2.2 2.2 0 1 0 5.5 7.7 A2.2 2.2 0 1 0 5.5 3.3 Z"/></svg>
      4170 W. Corwin Ave. Suite 310
    </div>
  </footer>
</main>
</body>
</html>
```